Modern Verdell Tree Care Website

I need a website for a full service Tree Care company. The company provides tree pruning, tree removal, tree preservation, emergency services, stump grinding, and emergency tree services.

Target Market(s)

Customers that need tree services

Industry/Entity Type

Landscaping, Tree Services

Coding

Coded - Design and coding required

Number of Pages Required

5+ page

Font styles to use
Sans Serif

Requirements
Must have
• Good clean design that showcases the services the company provides.
Nice to have
• Services page; contact form, blog, home page, about page

```html
<!DOCTYPE html>
<html lang="en">
<head>
<meta charset="utf-8">
<title>Verdell Tree Care</title>
<link href="https://fonts.googleapis.com/css2?family=Poppins:wght@400;500;600;700;800&display=swap" rel="stylesheet">
<style>
:root{
  --green:#7dc142;
  --green-dark:#3f7d1e;
  --green-form:#4c8a27;
  --pale:#f4faec;
  --card:#f1f8e6;
  --ink:#1d1d1d;
  --text:#555;
  --dark:#1f1f1f;
  --white:#fff;
}
*{box-sizing:border-box;margin:0;padding:0}
html,body{width:1200px;height:4484px;overflow:hidden}
body{font-family:"Poppins",sans-serif;color:var(--ink);background:var(--white);position:relative}
.wrap{width:920px;margin:0 auto;position:relative}
a{color:inherit;text-decoration:none}
.btn{display:inline-flex;align-items:center;gap:10px;background:var(--green);color:#fff;font-size:14px;font-weight:600;padding:0 24px;height:46px;border-radius:6px}
.btn svg{width:16px;height:16px}
.eyebrow{color:var(--green);font-size:12px;font-weight:500;letter-spacing:1px;text-transform:uppercase}
.title{font-size:38px;font-weight:700;line-height:1.2}
p{font-size:14px;line-height:1.75;color:var(--text)}

/* header */
.topbar{height:128px}
.topbar .wrap{display:flex;align-items:center;height:100%}
.brand{display:flex;align-items:center;gap:12px;font-weight:800;font-size:26px;color:var(--ink);line-height:1}
.brand .mark{width:34px;height:34px;background:var(--green)}
.contacts{display:flex;gap:48px;margin-left:auto}
.contact{display:flex;align-items:center;gap:12px}
.contact .ic{width:48px;height:48px;border:2px solid var(--green);border-radius:50%;display:flex;align-items:center;justify-content:center}
.contact .ic svg{width:20px;height:20px}
.contact b{display:block;font-size:15px}
.contact span{font-size:12px;color:var(--text)}

/* hero */
.hero{position:relative;height:584px}
.hero .photo{position:absolute;inset:0;background:linear-gradient(120deg,#3a4a22 0%,#6b6a3a 40%,#4a5a2a 70%,#2c3a1a 100%)}
.nav{position:absolute;top:0;left:140px;width:920px;height:60px;background:var(--dark);display:flex;align-items:center;z-index:2}
.nav a{color:#fff;font-size:15px;font-weight:500;margin-left:34px}
.nav a.active{color:var(--green)}
.nav .quote{margin-left:auto;background:var(--green);height:60px;display:flex;align-items:center;gap:10px;padding:0 28px;font-weight:600}
.hero h1{position:absolute;top:192px;width:100%;text-align:center;color:#fff;font-size:50px;font-weight:800;letter-spacing:1px}
.hero .btn{position:absolute;top:272px;left:50%;transform:translateX(-50%)}
.arrow{position:absolute;top:250px;width:20px;height:20px}
.arrow.l{left:80px}.arrow.r{right:80px}

/* about */
.about{background:var(--pale);height:608px}
.about .text{position:absolute;left:0;top:100px;width:430px}
.about .text .title{margin:14px 0 24px;font-size:34px}
.about .text .btn{margin-top:24px}
.about .media{position:absolute;left:508px;top:72px;width:352px;height:440px;background:linear-gradient(150deg,#7a6a4a,#c25a1a 40%,#5a4a32 75%,#3a3a2a)}
.about .block{position:absolute;left:752px;top:356px;width:132px;height:156px;background:var(--green)}
.about .play{position:absolute;left:464px;top:252px;width:88px;height:88px;border-radius:50%;background:var(--green);display:flex;align-items:center;justify-content:center;border:6px solid #fff}

/* services */
.services{height:860px;text-align:center}
.services .eyebrow{padding-top:84px;display:block}
.services .title{margin-top:10px}
.grid{display:grid;grid-template-columns:repeat(3,290px);gap:20px 25px;margin-top:52px;text-align:center}
.svc{background:var(--card);height:272px;padding-top:36px}
.svc .ic{width:64px;height:64px;border:2px solid var(--green);border-radius:50%;margin:0 auto;display:flex;align-items:center;justify-content:center}
.svc .ic svg{width:30px;height:30px}
.svc h3{font-size:18px;font-weight:600;margin:20px 0 8px}
.svc p{font-size:12px;line-height:1.6;padding:0 40px}
.svc .more{display:block;color:var(--green);font-size:13px;font-weight:600;margin-top:10px}
.svc.feature{background:var(--green);color:#fff;padding-top:76px}
.svc.feature h3{margin-top:0}
.svc.feature p{color:#fff}
.svc.feature .btn{background:#fff;color:var(--green);height:40px;margin-top:14px;font-size:13px}

/* cta */
.cta{position:relative;height:268px;text-align:center;color:#fff}
.cta .photo{position:absolute;inset:0;background:linear-gradient(90deg,#2a3a1e,#5a6a3e 50%,#3a4a26)}
.cta .inner{position:relative;padding-top:80px}
.cta h2{font-size:34px;font-weight:700}
.cta p{color:#eef;font-size:13px;width:640px;margin:10px auto 0;line-height:1.6;color:#e8e8e8}
.cta .btn{margin-top:16px}

/* why */
.why{height:852px}
.why .left{position:absolute;left:0;top:344px;width:440px}
.why .title{font-size:36px;margin:8px 0 24px}
.feats{display:grid;grid-template-columns:1fr 1fr;gap:24px 20px;margin-top:44px}
.feat{display:flex;gap:10px}
.feat svg{flex:0 0 38px;width:38px;height:38px}
.feat b{font-size:14px;color:var(--green);display:block;font-weight:600}
.feat span{font-size:11px;color:var(--text);line-height:1.5;display:block}
.form{position:absolute;left:480px;top:180px;width:440px;height:596px;background:var(--green-form);border-radius:14px;padding:40px 44px}
.form h3{color:#fff;font-size:16px;font-weight:600;margin-bottom:24px}
.field{background:rgba(0,0,0,.22);border-radius:6px;height:60px;margin-bottom:18px;color:#eaf3e0;font-size:13px;padding:0 20px;display:flex;align-items:center}
.field.msg{height:100px;align-items:flex-start;padding-top:20px}
.form .btn{background:#fff;color:var(--green-form);margin-top:10px}

/* blog */
.blog{height:904px;text-align:center}
.blog .eyebrow{display:block;padding-top:20px}
.blog .title{margin-top:6px}
.posts{display:grid;grid-template-columns:repeat(3,296px);gap:16px;margin-top:28px;text-align:left}
.post{height:512px;box-shadow:0 4px 16px rgba(0,0,0,.1);background:#fff}
.post .img{height:300px;position:relative}
.post:nth-child(1) .img{background:linear-gradient(160deg,#8a9a5a,#5a4a2a)}
.post:nth-child(2) .img{background:linear-gradient(160deg,#c8c0a0,#7a7050)}
.post:nth-child(3) .img{background:linear-gradient(160deg,#6a5a3a,#a06a3a)}
.date{position:absolute;left:24px;bottom:0;width:72px;height:96px;background:var(--green);color:#fff;text-align:center;padding-top:16px;line-height:1.2}
.date b{font-size:24px;display:block}
.date span{font-size:13px;font-weight:600}
.post .body{padding:24px 24px}
.post h4{font-size:18px;font-weight:700;margin-bottom:10px}
.post p{font-size:12px;line-height:1.7}
.post .more{display:block;color:var(--green);font-size:13px;font-weight:600;margin-top:10px}
.blog .all{margin-top:64px}

/* footer */
.footer{background:var(--dark);height:228px;color:#fff}
.footer .wrap{display:flex;padding-top:44px}
.col h5{font-size:14px;font-weight:600;margin-bottom:14px}
.col li{list-style:none;font-size:12px;color:#ddd;margin-bottom:7px;display:flex;align-items:center;gap:8px}
.col li .dot{width:14px;height:14px;border-radius:50%;background:var(--green)}
.col.q{width:212px}.col.c{width:288px}.col.f{width:200px}
.footer .brand{color:#fff;margin-left:auto;margin-top:40px}
.copy{background:var(--green);height:52px;display:flex;align-items:center;justify-content:center;color:#fff;font-size:13px;font-weight:500}
</style>
</head>
<body>

<header class="topbar">
  <div class="wrap">
    <div class="brand"><span class="mark"></span>Verdell Tree Care</div>
    <div class="contacts">
      <div class="contact"><div class="ic"><svg viewBox="0 0 24 24" fill="none" stroke="#7dc142" stroke-width="2"><path d="M5 3h4l2 5-3 2a12 12 0 0 0 6 6l2-3 5 2v4a2 2 0 0 1-2 2A18 18 0 0 1 3 5a2 2 0 0 1 2-2z"/></svg></div><div><b>Call</b><span>(555) 214-0387</span></div></div>
      <div class="contact"><div class="ic"><svg viewBox="0 0 24 24" fill="none" stroke="#7dc142" stroke-width="2"><rect x="3" y="5" width="18" height="14" rx="2"/><path d="M3 7l9 6 9-6"/></svg></div><div><b>Email</b><span>info@verdelltreecare.com</span></div></div>
      <div class="contact"><div class="ic"><svg viewBox="0 0 24 24" fill="none" stroke="#7dc142" stroke-width="2"><path d="M12 22s7-7 7-12a7 7 0 0 0-14 0c0 5 7 12 7 12z"/><circle cx="12" cy="10" r="2.5"/></svg></div><div><b>Location</b><span>Lorem ipsum is simply dummy text</span></div></div>
    </div>
  </div>
</header>

<section class="hero">
  <div class="photo" role="img" aria-label="Arborist in a helmet cutting a tree trunk with a chainsaw"></div>
  <nav class="nav">
    <a class="active" href="#">[ Home ]</a><a href="#">Services</a><a href="#">About Us</a><a href="#">Blog</a><a href="#">Contact</a>
    <a class="quote" href="#">Get A Quote <svg width="16" height="16" viewBox="0 0 16 16" fill="none" stroke="#fff" stroke-width="2"><path d="M2 8h11M9 4l4 4-4 4"/></svg></a>
  </nav>
  <svg class="arrow l" viewBox="0 0 20 20" fill="none" stroke="#fff" stroke-width="2.5"><path d="M13 3l-7 7 7 7"/></svg>
  <svg class="arrow r" viewBox="0 0 20 20" fill="none" stroke="#fff" stroke-width="2.5"><path d="M7 3l7 7-7 7"/></svg>
  <h1>LET'S START YOUR SERVICES</h1>
  <a class="btn" href="#">Contact Now <svg viewBox="0 0 16 16" fill="none" stroke="#fff" stroke-width="2"><path d="M2 8h11M9 4l4 4-4 4"/></svg></a>
</section>

<section class="about">
  <div class="wrap">
    <div class="text">
      <span class="eyebrow">About Us</span>
      <h2 class="title">VerdellTreeCare Landscaping Tree Services</h2>
      <p>Lorem ipsum dolor sit amet, consectetur adipiscing elit, sed do eiusmod tempor incididunt ut labore et dolore magna aliqua. Quis ipsum suspendisse ultrices gravida. Risus commodo viverra maecenas accumsan lacus vel facilisis. Lorem ipsum dolor sit amet, consectetur adipiscing elit, sed do eiusmod tempor incididunt ut labore et dolore magna aliqua. Quis ipsum suspendisse ultrices gravida. Risus commodo viverra maecenas accumsan lacus vel facilisis.</p>
      <a class="btn" href="#">Read More <svg viewBox="0 0 16 16" fill="none" stroke="#fff" stroke-width="2"><path d="M2 8h11M9 4l4 4-4 4"/></svg></a>
    </div>
    <div class="block"></div>
    <div class="media" role="img" aria-label="Worker operating a sawmill cutting a large log"></div>
    <div class="play"><svg width="28" height="28" viewBox="0 0 28 28"><path d="M9 5l15 9-15 9z" fill="#fff"/></svg></div>
  </div>
</section>

<section class="services">
  <div class="wrap">
    <span class="eyebrow">Our Services</span>
    <h2 class="title">Landscaping Tree Services</h2>
    <div class="grid">
      <div class="svc"><div class="ic"><svg viewBox="0 0 30 30" fill="none" stroke="#7dc142" stroke-width="2"><circle cx="15" cy="11" r="7"/><path d="M15 18v9M11 27h8"/></svg></div><h3>Tree Pruning</h3><p>Lorem ipsum dolor sit amet, eiusmod incididunt ut labore et dolore magna aliqua.</p><a class="more" href="#">Read More</a></div>
      <div class="svc"><div class="ic"><svg viewBox="0 0 30 30" fill="none" stroke="#7dc142" stroke-width="2"><path d="M15 3l8 12H7z"/><path d="M15 15v12M11 27h8"/></svg></div><h3>Tree Removal</h3><p>Lorem ipsum dolor sit amet, eiusmod incididunt ut labore et dolore magna aliqua.</p><a class="more" href="#">Read More</a></div>
      <div class="svc"><div class="ic"><svg viewBox="0 0 30 30" fill="none" stroke="#7dc142" stroke-width="2"><path d="M15 3c6 4 6 14 0 18-6-4-6-14 0-18z"/><path d="M15 10v17"/></svg></div><h3>Tree Preservation</h3><p>Lorem ipsum dolor sit amet, eiusmod incididunt ut labore et dolore magna aliqua.</p><a class="more" href="#">Read More</a></div>
      <div class="svc"><div class="ic"><svg viewBox="0 0 30 30" fill="none" stroke="#7dc142" stroke-width="2"><circle cx="15" cy="15" r="11"/><path d="M15 8v8l5 3"/></svg></div><h3>Emergency Services</h3><p>Lorem ipsum dolor sit amet, eiusmod incididunt ut labore et dolore magna aliqua.</p><a class="more" href="#">Read More</a></div>
      <div class="svc"><div class="ic"><svg viewBox="0 0 30 30" fill="none" stroke="#7dc142" stroke-width="2"><ellipse cx="15" cy="12" rx="10" ry="4"/><path d="M5 12v8c0 2 4 4 10 4s10-2 10-4v-8"/></svg></div><h3>Stump Grinding</h3><p>Lorem ipsum dolor sit amet, eiusmod incididunt ut labore et dolore magna aliqua.</p><a class="more" href="#">Read More</a></div>
      <div class="svc feature"><h3>VerdellTreeCare</h3><p>Lorem ipsum dolor sit amet, eiusmod incididunt ut labore et dolore magna aliqua.</p><a class="btn" href="#">View All Services</a></div>
    </div>
  </div>
</section>

<section class="cta">
  <div class="photo" role="img" aria-label="Family watering and tending plants in a garden"></div>
  <div class="inner">
    <h2>Transform Your Landscape With VerdellTreeCare!</h2>
    <p>Enhance the beauty and health of your outdoor space with our tree services. Whether you need tree trimming, removal, or landscaping care, we are here to help.</p>
    <a class="btn" href="#">BOOK NOW <svg viewBox="0 0 16 16" fill="none" stroke="#fff" stroke-width="2"><path d="M2 8h11M9 4l4 4-4 4"/></svg></a>
  </div>
</section>

<section class="why">
  <div class="wrap">
    <div class="left">
      <span class="eyebrow">Contact Form</span>
      <h2 class="title">Why Most of The People Choose Us</h2>
      <p>Lorem ipsum dolor sit amet, consectetur adipiscing elit, sed do eiusmod tempor incididunt ut labore et dolore magna aliqua. Quis ipsum suspendisse ultrices gravida. Risus commodo viverra maecenas accumsan lacus vel facilisis.</p>
      <div class="feats">
        <div class="feat"><svg viewBox="0 0 38 38" fill="none" stroke="#7dc142" stroke-width="2"><circle cx="19" cy="19" r="15"/><path d="M19 10v9l6 4"/></svg><div><b>Available 24/7</b><span>Lorem ipsum dolor sit amet, consectetur adipiscing elit, sed do eiusmod tempor.</span></div></div>
        <div class="feat"><svg viewBox="0 0 38 38" fill="none" stroke="#7dc142" stroke-width="2"><rect x="7" y="5" width="24" height="28" rx="2"/><path d="M12 13h14M12 19h14M12 25h8"/></svg><div><b>Free quotation</b><span>Lorem ipsum dolor sit amet, consectetur adipiscing elit, sed do eiusmod tempor.</span></div></div>
        <div class="feat"><svg viewBox="0 0 38 38" fill="none" stroke="#7dc142" stroke-width="2"><path d="M19 4c8 5 8 20 0 26-8-6-8-21 0-26z"/><path d="M19 14v20"/></svg><div><b>Creative Ideas</b><span>Lorem ipsum dolor sit amet, consectetur adipiscing elit, sed do eiusmod tempor.</span></div></div>
        <div class="feat"><svg viewBox="0 0 38 38" fill="none" stroke="#7dc142" stroke-width="2"><circle cx="19" cy="13" r="6"/><path d="M7 33c0-7 5-11 12-11s12 4 12 11"/></svg><div><b>Customer Focused</b><span>Lorem ipsum dolor sit amet, consectetur adipiscing elit, sed do eiusmod tempor.</span></div></div>
      </div>
    </div>
    <form class="form">
      <h3>Free Estimate</h3>
      <div class="field">Name</div>
      <div class="field">Email</div>
      <div class="field">Phone No.</div>
      <div class="field msg">Your Message Here</div>
      <span class="btn">Submit Now <svg viewBox="0 0 16 16" fill="none" stroke="#4c8a27" stroke-width="2"><path d="M2 8h11M9 4l4 4-4 4"/></svg></span>
    </form>
  </div>
</section>

<section class="blog">
  <div class="wrap">
    <span class="eyebrow">Our Blog</span>
    <h2 class="title">Recent Blogs</h2>
    <div class="posts">
      <article class="post"><div class="img" role="img" aria-label="Worker splitting logs in a forest"><div class="date"><b>09</b><span>MAY</span></div></div><div class="body"><h4>Lorem ipsum dolor sit</h4><p>Lorem ipsum dolor sit amet, consectetur adipiscing elit, sed do eiusmod tempor incididunt ut labore et dolore. Quis ipsum suspendisse ultrices.</p><a class="more" href="#">Read More</a></div></article>
      <article class="post"><div class="img" role="img" aria-label="Tall tree trunks in a sunlit forest"><div class="date"><b>09</b><span>MAY</span></div></div><div class="body"><h4>Lorem ipsum dolor sit</h4><p>Lorem ipsum dolor sit amet, consectetur adipiscing elit, sed do eiusmod tempor incididunt ut labore et dolore. Quis ipsum suspendisse ultrices.</p><a class="more" href="#">Read More</a></div></article>
      <article class="post"><div class="img" role="img" aria-label="Chainsaw cutting through stacked timber"><div class="date"><b>09</b><span>MAY</span></div></div><div class="body"><h4>Lorem ipsum dolor sit</h4><p>Lorem ipsum dolor sit amet, consectetur adipiscing elit, sed do eiusmod tempor incididunt ut labore et dolore. Quis ipsum suspendisse ultrices.</p><a class="more" href="#">Read More</a></div></article>
    </div>
    <a class="btn all" href="#">View All Blogs <svg viewBox="0 0 16 16" fill="none" stroke="#fff" stroke-width="2"><path d="M2 8h11M9 4l4 4-4 4"/></svg></a>
  </div>
</section>

<footer class="footer">
  <div class="wrap">
    <div class="col q"><h5>QUICK LINKS</h5><ul><li>Home</li><li>About Us</li><li>Services</li><li>Blog</li><li>Contact</li></ul></div>
    <div class="col c"><h5>CONTACT DETAILS</h5><ul><li><span class="dot"></span>Lorem ipsum dolor sit amet</li><li><span class="dot"></span>Phone (555) 214-0387</li><li><span class="dot"></span>info@verdelltreecare.com</li></ul></div>
    <div class="col f"><h5>FOLLOW US</h5><ul><li><span class="dot"></span>Friendbook</li><li><span class="dot"></span>Chirper</li><li><span class="dot"></span>Viewtube</li><li><span class="dot"></span>Snapgram</li></ul></div>
    <div class="brand"><span class="mark"></span>Verdell Tree Care</div>
  </div>
</footer>
<div class="copy">Copyright © 2024 VerdellTreeCare Landscaping Tree Services</div>

</body>
</html>
```